Recovery Lounge

We are opening a recovering lounge in our physical therapy clinic. We would like a menu of our services that we can offer guest. We would like it to flow well with our brand. Ive attached a doc of our prices an basic idea of what we are looking for.

our website is tovimeptclinic.com if your need brand inspiration.

```html
<!DOCTYPE html>
<html lang="en">
<head>
<meta charset="utf-8">
<title>Recovery Lounge – Tovime</title>
<link href="https://fonts.googleapis.com/css2?family=Figtree:wght@500;600;700;800&family=Lexend:wght@300;400;500;600&display=swap" rel="stylesheet">
<style>
  :root {
    --navy: #29256a;
    --navy-deep: #361f78;
    --ring: #4f4a9a;
    --coral: #ef6345;
    --cream: #fbeed6;
    --cream-light: #fffaf2;
    --ink: #2b2b2b;
    --purple-text: #3a2a8c;
    --white: #ffffff;
  }
  * { box-sizing: border-box; margin: 0; padding: 0; }
  html, body { width: 970px; height: 1200px; overflow: hidden; background: var(--navy); }
  .poster { position: relative; width: 970px; height: 1200px; overflow: hidden; background: var(--navy); font-family: "Lexend", sans-serif; color: var(--ink); }
  .backdrop { position: absolute; inset: 0; }
  .title { position: absolute; top: 40px; left: 0; width: 100%; text-align: center; font-family: "Figtree", sans-serif; font-weight: 800; font-size: 74px; color: var(--white); letter-spacing: -1px; }
  .title .accent { color: var(--coral); }
  .panel { position: absolute; left: 60px; top: 380px; width: 853px; height: 722px; border-radius: 0 0 60px 60px; background: linear-gradient(180deg, var(--white) 0%, var(--cream-light) 25%, var(--cream) 100%); }
  .brand-disc { position: absolute; left: 129px; top: 173px; width: 304px; height: 304px; border-radius: 50%; background: linear-gradient(180deg, var(--ring) 0%, var(--ring) 45%, rgba(255,255,255,0) 75%); }
  .brand-disc-inner { position: absolute; left: 17px; top: 17px; width: 270px; height: 270px; border-radius: 50%; background: linear-gradient(180deg, var(--white) 60%, var(--cream-light) 100%); display: flex; align-items: center; justify-content: center; }
  .brand-name { font-family: "Lexend", sans-serif; font-weight: 500; font-size: 58px; color: var(--purple-text); letter-spacing: -1px; }
  .photo { position: absolute; left: 430px; top: 330px; width: 483px; height: 200px;
    background:
      radial-gradient(ellipse 22% 38% at 42% 40%, rgba(205,150,105,0.55) 0%, rgba(205,150,105,0) 100%),
      radial-gradient(ellipse 60% 45% at 30% 80%, rgba(235,235,238,0.9) 0%, rgba(235,235,238,0) 100%),
      linear-gradient(90deg, rgba(255,255,255,0) 0%, rgba(240,238,240,0.8) 30%, #ececf0 70%, #e7e7ec 100%);
    -webkit-mask-image: linear-gradient(180deg, rgba(0,0,0,0) 0%, #000 25%, #000 85%, rgba(0,0,0,0) 100%);
    mask-image: linear-gradient(180deg, rgba(0,0,0,0) 0%, #000 25%, #000 85%, rgba(0,0,0,0) 100%); }
  .section-title { position: absolute; left: 126px; font-family: "Figtree", sans-serif; font-weight: 800; color: var(--coral); }
  .alacarte-title { top: 522px; font-size: 38px; }
  .menu { position: absolute; left: 126px; top: 573px; list-style: none; }
  .menu li { display: flex; align-items: center; height: 26px; font-size: 21px; font-weight: 300; color: var(--ink); }
  .menu .tick { width: 17px; height: 17px; margin-right: 5px; flex: none; }
  .price { font-weight: 600; color: var(--purple-text); margin-left: 6px; }
  .bundles-title { top: 735px; font-size: 37px; }
  .bundles-title .note { font-family: "Lexend", sans-serif; font-weight: 400; color: var(--ink); }
  .safety { position: absolute; left: 611px; top: 531px; width: 260px; height: 260px; border-radius: 50%; background: var(--coral); display: flex; align-items: center; justify-content: center; }
  .safety::after { content: ""; position: absolute; inset: 10px; border-radius: 50%; border: 1.5px solid var(--white); }
  .safety p { width: 196px; text-align: center; font-family: "Figtree", sans-serif; font-weight: 700; font-size: 20px; line-height: 1.35; color: var(--white); }
  .bundle { position: absolute; width: 350px; }
  .bundle h3 { font-family: "Figtree", sans-serif; font-weight: 700; font-size: 28px; color: var(--ink); letter-spacing: -0.3px; }
  .bundle h3 .cost { color: var(--coral); }
  .bundle .save { font-family: "Figtree", sans-serif; font-weight: 800; font-size: 18px; color: var(--purple-text); margin-top: 1px; }
  .bundle .items { font-weight: 300; font-style: italic; font-size: 16.5px; color: var(--coral); margin-top: 4px; line-height: 1.3; }
  .reset { left: 126px; top: 811px; }
  .refresh { left: 527px; top: 811px; }
  .restore { left: 126px; top: 954px; }
  .rejuvenate { left: 527px; top: 954px; }
  .restore .items { padding-left: 8px; }
  .divider-v { position: absolute; left: 487px; top: 806px; height: 240px; border-left: 1.5px dashed #555; }
  .divider-h { position: absolute; top: 936px; border-top: 1.5px dashed #555; }
  .divider-h.left { left: 128px; width: 327px; }
  .divider-h.right { left: 531px; width: 326px; }
  .footer { position: absolute; left: 0; top: 1122px; width: 100%; display: flex; align-items: center; justify-content: center; gap: 12px; }
  .footer .globe { width: 30px; height: 30px; }
  .footer .url { font-family: "Lexend", sans-serif; font-weight: 600; font-size: 36px; letter-spacing: 2px; color: var(--white); }
</style>
</head>
<body>
<div class="poster">
  <svg class="backdrop" width="970" height="1200" viewBox="0 0 970 1200" aria-hidden="true">
    <defs>
      <linearGradient id="bottomBand" x1="0" y1="0" x2="0" y2="1">
        <stop offset="0" stop-color="#2d2670"/>
        <stop offset="1" stop-color="#3a1f7a"/>
      </linearGradient>
    </defs>
    <rect width="970" height="1200" fill="var(--navy)"/>
    <path d="M0 345 C 120 380, 300 440, 450 345 C 580 270, 760 260, 870 320 C 910 345, 950 390, 970 420 L970 1010 L0 1010 Z" fill="var(--white)"/>
    <path d="M0 345 C 120 380, 300 440, 450 345 C 580 270, 760 260, 870 320 C 910 345, 950 390, 970 420 L970 385 C 945 350, 910 310, 870 295 C 760 250, 580 255, 450 330 C 300 420, 120 370, 0 320 Z" fill="var(--coral)"/>
    <rect x="0" y="1010" width="970" height="190" fill="url(#bottomBand)"/>
    <rect x="0" y="1022" width="970" height="7" fill="var(--coral)"/>
  </svg>

  <h1 class="title">Recovery <span class="accent">Lounge</span></h1>

  <div class="panel"></div>

  <div class="brand-disc">
    <div class="brand-disc-inner"><span class="brand-name">tovime</span></div>
  </div>

  <div class="photo" role="img" aria-label="Photo of a woman resting on a white contoured pillow, wearing a white robe"></div>

  <h2 class="section-title alacarte-title">A la carte</h2>
  <ul class="menu">
    <li><svg class="tick" viewBox="0 0 20 20"><circle cx="10" cy="10" r="8.5" fill="none" stroke="#3a2a8c" stroke-width="1.4"/><path d="M6 10.2l2.7 2.7L14 7.6" fill="none" stroke="#3a2a8c" stroke-width="1.6" stroke-linecap="round" stroke-linejoin="round"/></svg>Infrared Sauna + Red Light (30 min)<span class="price">$40</span></li>
    <li><svg class="tick" viewBox="0 0 20 20"><circle cx="10" cy="10" r="8.5" fill="none" stroke="#3a2a8c" stroke-width="1.4"/><path d="M6 10.2l2.7 2.7L14 7.6" fill="none" stroke="#3a2a8c" stroke-width="1.6" stroke-linecap="round" stroke-linejoin="round"/></svg>Infrared Sauna + Red Light (60 min)<span class="price">$65</span></li>
    <li><svg class="tick" viewBox="0 0 20 20"><circle cx="10" cy="10" r="8.5" fill="none" stroke="#3a2a8c" stroke-width="1.4"/><path d="M6 10.2l2.7 2.7L14 7.6" fill="none" stroke="#3a2a8c" stroke-width="1.6" stroke-linecap="round" stroke-linejoin="round"/></svg>AirFlex Compression (30 min)<span class="price">$40</span></li>
    <li><svg class="tick" viewBox="0 0 20 20"><circle cx="10" cy="10" r="8.5" fill="none" stroke="#3a2a8c" stroke-width="1.4"/><path d="M6 10.2l2.7 2.7L14 7.6" fill="none" stroke="#3a2a8c" stroke-width="1.6" stroke-linecap="round" stroke-linejoin="round"/></svg>AirFlex Compression (60 min)<span class="price">$65</span></li>
    <li><svg class="tick" viewBox="0 0 20 20"><circle cx="10" cy="10" r="8.5" fill="none" stroke="#3a2a8c" stroke-width="1.4"/><path d="M6 10.2l2.7 2.7L14 7.6" fill="none" stroke="#3a2a8c" stroke-width="1.6" stroke-linecap="round" stroke-linejoin="round"/></svg>Paraffin Hand Bath (15 min)<span class="price">$25</span></li>
  </ul>

  <div class="safety"><p>For safety, a rest/cool-down period is required after 30 minutes in the sauna.</p></div>

  <h2 class="section-title bundles-title">Bundles <span class="note">(best sellers)</span></h2>

  <div class="bundle reset">
    <h3>Reset (45 min) <span class="cost">$55</span></h3>
    <p class="save">(Save $10)</p>
    <p class="items">Choose 1: Sauna (30) or AirFlex (30)<br>+ Paraffin Hand Bath</p>
  </div>
  <div class="bundle refresh">
    <h3>Refresh (60 min) <span class="cost">$65</span></h3>
    <p class="save">(Save $15)</p>
    <p class="items">Sauna (30) + AirFlex (30)</p>
  </div>
  <div class="bundle restore">
    <h3>Restore (75 min) <span class="cost">$85</span></h3>
    <p class="save">(Save $20)</p>
    <p class="items">Sauna (30) + AirFlex (30) + Paraffin</p>
  </div>
  <div class="bundle rejuvenate">
    <h3>Rejuvenate (130 min) <span class="cost">$130</span></h3>
    <p class="save">(Save $25)</p>
    <p class="items">Sauna (60) + AirFlex (60) + Paraffin</p>
  </div>

  <div class="divider-v"></div>
  <div class="divider-h left"></div>
  <div class="divider-h right"></div>

  <div class="footer">
    <svg class="globe" viewBox="0 0 30 30" aria-hidden="true">
      <g fill="none" stroke="#ef6345" stroke-width="1.6">
        <circle cx="15" cy="15" r="13"/>
        <ellipse cx="15" cy="15" rx="6" ry="13"/>
        <line x1="2" y1="15" x2="28" y2="15"/>
        <path d="M4.5 8.5h21M4.5 21.5h21"/>
      </g>
    </svg>
    <span class="url">www.tovimeptclinic.com</span>
  </div>
</div>
</body>
</html>
```